KRL Stationery Design Project

Dear Designers,
We need a new stationery design for company to match our new logo.
Designers should provide a design for the following:
1. Business Card: 3.5x2 Inches.
2. Letterhead: A4 size.
3. Envelops: 25x35.5 Cm.
You can keep the Arabic name at the bottom of the logo Or you can use the separate attached Arabic Name.
Please refer to the attached logo guide for design information.
Sample Business Card information:
Name: Tarek Sowan
Position: Operation Manager
Tel: +966 920007164 Ex. 500
Fax: +966 (3)8842617
Mob: +966 (5)00263817
email: tarek@krl-example.com.sa
URL: www.krl-example.com.sa
Address:
Nakheel Heights, Suite 718
Zayed bin Omar Str.
Khobar, 31847
Saudi Arabia
Updates
Dear All,
Please note, we had uploaded our logo along with Arabic writing in Adobe illustrator format (.ai).
Regards,
Karim
Dear All,
A sample data for the business card had been added as per your request.
Regards,
Karim

```html
<!DOCTYPE html>
<html lang="en">
<head>
<meta charset="utf-8">
<title>KRL Business Card</title>
<link rel="stylesheet" href="https://fonts.googleapis.com/css2?family=Source+Sans+3:wght@400;600&display=swap">
<style>
  :root {
    --stage: #262829;
    --card: #0b2c4d;
    --ink: #ffffff;
    --rule: #8a97a6;
    --shadow: rgba(0, 0, 0, 0.55);
  }
  * { margin: 0; padding: 0; box-sizing: border-box; }
  html, body {
    width: 960px;
    height: 1200px;
    overflow: hidden;
    background: var(--stage);
  }
  body {
    position: relative;
    font-family: "Source Sans 3", "Myriad Pro", Arial, sans-serif;
    color: var(--ink);
  }
  .card {
    position: absolute;
    left: 60px;
    width: 840px;
    height: 478px;
    background: var(--card);
    border-radius: 28px;
    box-shadow: 0 6px 18px var(--shadow);
  }
  .card--front { top: 82px; }
  .card--back { top: 643px; }

  .brand {
    position: absolute;
    display: flex;
    align-items: center;
    gap: 18px;
    font-weight: 600;
    line-height: 1;
    color: var(--ink);
    letter-spacing: 2px;
  }
  .brand__dot {
    width: 22px;
    height: 22px;
    border-radius: 50%;
    background: var(--ink);
  }
  .card--front .brand { left: 44px; top: 72px; font-size: 120px; }
  .card--back .brand {
    left: 50%;
    top: 50%;
    transform: translate(-50%, -50%);
    font-size: 130px;
  }

  .person { position: absolute; left: 28px; top: 308px; }
  .person__name { font-size: 25px; font-weight: 400; line-height: 30px; }
  .person__role { font-size: 19px; line-height: 28px; }

  .rule {
    position: absolute;
    left: 28px;
    right: 35px;
    top: 380px;
    height: 2px;
    background: var(--rule);
  }

  .contact {
    position: absolute;
    top: 397px;
    font-size: 19px;
    line-height: 28px;
    list-style: none;
  }
  .contact li { display: flex; align-items: center; gap: 6px; white-space: nowrap; }
  .contact svg { width: 15px; height: 15px; fill: var(--ink); flex: none; }
  .contact--phones { left: 28px; }
  .contact--online { left: 237px; }
  .contact--address { right: 36px; text-align: right; }
  .contact--address li { justify-content: flex-end; }
</style>
</head>
<body>

<section class="card card--front">
  <div class="brand"><span class="brand__dot"></span>KRL</div>

  <div class="person">
    <p class="person__name">Your Name</p>
    <p class="person__role">Designation</p>
  </div>

  <div class="rule"></div>

  <ul class="contact contact--phones">
    <li>
      <svg viewBox="0 0 16 16" aria-hidden="true"><path d="M1 6c0-3 3-4 7-4s7 1 7 4v1h-4V5H5v2H1zM3 8h10l1 6H2zm5 1.5a2 2 0 1 0 0 4 2 2 0 0 0 0-4z"/></svg>
      123-123-1234
    </li>
    <li>
      <svg viewBox="0 0 16 16" aria-hidden="true"><path d="M4 1h8v4H4zM1 6h14v6h-3v3H4v-3H1zm4 4v4h6v-4z"/></svg>
      123-123-1234
    </li>
  </ul>

  <ul class="contact contact--online">
    <li>
      <svg viewBox="0 0 16 16" aria-hidden="true"><path d="M8 1a7 7 0 1 0 3.5 13l-.7-1.3A5.5 5.5 0 1 1 13.5 8v1a1 1 0 0 1-2 0V4.5H10v.6A3.5 3.5 0 1 0 10.4 11 2.5 2.5 0 0 0 15 9V8a7 7 0 0 0-7-7zm0 5a2 2 0 1 1 0 4 2 2 0 0 1 0-4z"/></svg>
      info@krl-example.com.sa
    </li>
    <li>
      <svg viewBox="0 0 16 16" aria-hidden="true"><path d="M8 1a7 7 0 1 0 0 14A7 7 0 0 0 8 1zm4.9 6h-2.4a11 11 0 0 0-.9-4.2A5.5 5.5 0 0 1 12.9 7zM8 2.6c.6.9 1 2.5 1.1 4.4H6.9C7 5.1 7.4 3.5 8 2.6zM6.4 2.8A11 11 0 0 0 5.5 7H3.1a5.5 5.5 0 0 1 3.3-4.2zM3.1 9h2.4a11 11 0 0 0 .9 4.2A5.5 5.5 0 0 1 3.1 9zM8 13.4c-.6-.9-1-2.5-1.1-4.4h2.2c-.1 1.9-.5 3.5-1.1 4.4zm1.6-.2a11 11 0 0 0 .9-4.2h2.4a5.5 5.5 0 0 1-3.3 4.2z"/></svg>
      www.krl-example.com.sa
    </li>
  </ul>

  <ul class="contact contact--address">
    <li>1234, Suite# 123, Street Name</li>
    <li>State NAME, Country Code</li>
  </ul>
</section>

<section class="card card--back">
  <div class="brand"><span class="brand__dot"></span>KRL</div>
</section>

</body>
</html>
```